Thoroughbred Racing Partnership needs web design

Glimmer of Laurel Partners is a management group who buys horses and races them on both the West and East coasts. The premise of the business is for an investment as little as $500, anyone can be a partner and own a percentage of a horse(s). This is a low cost way of getting involved in the exciting sport of Thoroughbred Racing, without shouldering the heavy financial responsibility. Our target market is mostly males 40+ but we want to include all target markets. We are looking for something very clean and professional, we want to give an image of success. Nothing overly "artsy." I have included the logo in which you can incorporate in the site. Also, the logo colors will be the colors of our "silks." The silks are what the jockey wears and will be an important marketing tool for GOL. We would like a very prominent picture of a racehorse somewhere on the homepage, we want to make it clear that is a website for Horseracing partnerships.

On the top of the site, it should say "Glimmer of Laurel" (on the top)
and below that "Thoroughbred Racing Partnerships." (below that)

The main sections, which should be across the top are:

Home
About Us
Ownership
Stable Roster
News
Contact us

Some of these will have drop down menus.

An example of a competitor website that we like is: www.harrowgatefarm.example
An example of a competitor website that we don't like is: www.paddockvue.example
Updates

Project Deadline Extended
Reason: We have a Board of Directors meeting on the 22nd and we will be making a decision on that day. I'm giving an extension so that all designers are able to submit their designs by the 22nd. Thank you!

Target Market(s)

40+ males

Industry/Entity Type

Business

Requirements
Must have
• our logo must be on the site. We would like at least one bold image of a thoroughbred horse in action. The picture is going to tell the story so it needs to be very eye-catching.

Our slogan should also be included on the website, "Experience the thrill of owning a Racehorse."
Should not have
• cartoons, artsy pictures, pictures of Steeplechase horses or "jumpers." This partnership is for racehorses only, there is not jumping involved with the horses.

```html
<!DOCTYPE html>
<html lang="en">
<head>
<meta charset="utf-8">
<title>Glimmer of Laurel Partners – Thoroughbred Racing Partnerships</title>
<link href="https://fonts.googleapis.com/css2?family=PT+Serif:wght@700&family=Source+Sans+3:wght@400;600&display=swap" rel="stylesheet">
<style>
  :root {
    --navy: #0f3a63;
    --navy-dark: #0a2c4d;
    --blue-head: #386c9b;
    --link-blue: #2e6aa3;
    --text: #555a60;
    --muted: #7c8086;
    --header-bg-top: #f2f6f9;
    --header-bg-bottom: #e3ebf1;
    --footer-bg: #1e1e1e;
    --footer-text: #b4b4b4;
    --white: #ffffff;
  }
  * { margin: 0; padding: 0; box-sizing: border-box; }
  html, body { width: 1200px; height: 1051px; overflow: hidden; }
  body {
    position: relative;
    background: var(--white);
    font-family: "Source Sans 3", "Myriad Pro", Arial, sans-serif;
    color: var(--text);
  }
  .site-header {
    position: absolute; left: 0; top: 0; width: 1200px; height: 159px;
    background: linear-gradient(var(--header-bg-top), var(--header-bg-bottom));
    border-bottom: 1px solid #d3d9de;
  }
  .brand {
    position: absolute; left: 100px; top: 30px;
    display: flex; align-items: center; gap: 12px;
    font-family: "PT Serif", Georgia, serif; font-weight: 700;
    font-size: 38px; color: var(--navy); letter-spacing: 1px;
  }
  .brand-mark { width: 26px; height: 26px; border-radius: 50%; background: var(--navy); }
  .brand-name { line-height: 1; }
  .brand small { display: block; font-size: 22px; letter-spacing: 0.5px; line-height: 1; margin-top: 4px; }
  .site-title { position: absolute; right: 101px; top: 26px; text-align: right; white-space: nowrap; }
  .site-title h1 {
    font-family: "PT Serif", Georgia, serif; font-weight: 700;
    font-size: 35px; color: #3b3f44; letter-spacing: 0.5px; line-height: 1.1;
  }
  .site-title p { font-size: 22px; color: #4d5157; margin-top: 6px; }

  .main-nav {
    position: absolute; left: 99px; top: 134px; width: 1002px; height: 48px;
    background: linear-gradient(#1f5384, var(--navy-dark));
    border: 1px solid #082440; border-radius: 3px;
    display: flex; align-items: center; white-space: nowrap;
  }
  .main-nav a {
    flex: none; text-align: center;
    color: #c9d8e6; text-decoration: none; font-weight: 600; font-size: 15px;
    letter-spacing: 0.3px; border-right: 1px solid #3d6a94; line-height: 24px;
  }
  .main-nav a.home { width: 90px; color: var(--white); }
  .main-nav a.about { width: 122px; }
  .main-nav a.ownership { width: 133px; }
  .main-nav a.roster { width: 157px; }
  .main-nav a.news { width: 90px; }
  .main-nav a.contact { width: 141px; }
  .nav-social {
    flex: none; margin-left: auto; margin-right: 15px; display: flex; align-items: center; gap: 9px;
    color: #c9d8e6; font-weight: 600; font-size: 15px;
  }
  .nav-social .join { margin-right: 4px; }
  .social-dot { width: 26px; height: 26px; border-radius: 50%; background: #6f9cc6; display: flex; align-items: center; justify-content: center; }

  .hero {
    position: absolute; left: 99px; top: 196px; width: 1002px; height: 492px;
    border-radius: 3px; overflow: hidden;
  }
  .hero-photo {
    position: absolute; inset: 0;
    background: linear-gradient(100deg, #3f6fa6 0%, #5b87bb 35%, #8a6a55 48%, #7b9cc4 62%, #9db6d3 100%);
  }
  .hero-title {
    position: absolute; left: 0; right: 0; top: 38px; text-align: center; white-space: nowrap;
    font-family: "PT Serif", Georgia, serif; font-weight: 700; font-size: 31px;
    color: var(--white); letter-spacing: 0.5px; text-shadow: 0 2px 4px rgba(0,0,0,0.35);
  }
  .slider-prev {
    position: absolute; left: 21px; top: 224px; width: 42px; height: 42px; border-radius: 50%;
    background: rgba(225,233,242,0.9); display: flex; align-items: center; justify-content: center;
  }
  .news-box {
    position: absolute; left: 731px; top: 138px; width: 250px; height: 331px;
    background: var(--white); box-shadow: 0 2px 6px rgba(0,0,0,0.25); padding: 16px 20px 0 22px;
  }
  .news-box h2 {
    font-family: "PT Serif", Georgia, serif; font-weight: 700; font-size: 21px;
    color: var(--blue-head); text-align: center; padding-bottom: 12px;
    border-bottom: 1px solid #e9eef2; margin-bottom: 20px;
  }
  .news-item { display: flex; gap: 10px; margin-bottom: 21px; }
  .news-item svg { flex: none; margin-top: 4px; }
  .news-item a { display: block; color: var(--link-blue); text-decoration: none; font-size: 15px; line-height: 21px; }
  .news-item time { display: block; font-size: 13px; color: var(--muted); margin-top: 1px; }

  .welcome { position: absolute; left: 101px; top: 720px; width: 672px; }
  .welcome h2 {
    font-family: "PT Serif", Georgia, serif; font-weight: 700; font-size: 21px;
    color: var(--blue-head); letter-spacing: 0.3px;
  }
  .welcome p { margin-top: 14px; font-size: 14.5px; line-height: 25px; text-align: justify; color: var(--text); }

  .video {
    position: absolute; left: 792px; top: 729px; width: 308px; height: 174px; border-radius: 3px; overflow: hidden;
  }
  .video-still { position: absolute; inset: 0; background: linear-gradient(90deg, #5c6470, #2b2f36 45%, #4a4f58 75%, #6a6e76); }
  .video-play { position: absolute; left: 121px; top: 54px; }

  .site-footer {
    position: absolute; left: 0; top: 944px; width: 1200px; height: 107px; background: var(--footer-bg);
  }
  .footer-nav { position: absolute; left: 99px; top: 27px; display: flex; font-size: 13.5px; white-space: nowrap; }
  .footer-nav a { color: var(--footer-text); text-decoration: none; padding: 0 10px; border-right: 1px solid #8a8a8a; line-height: 14px; }
  .footer-nav a:first-child { padding-left: 0; }
  .footer-nav a:last-child { border-right: none; }
  .copyright { position: absolute; left: 99px; top: 62px; font-size: 13.5px; color: var(--footer-text); white-space: nowrap; }
  .footer-social { position: absolute; right: 100px; top: 41px; display: flex; gap: 9px; }
  .footer-social .social-dot { background: #5a5a5a; }
</style>
</head>
<body>
  <header class="site-header">
    <div class="brand">
      <span class="brand-mark"></span>
      <span class="brand-name">GOL<small>PARTNERS.COM</small></span>
    </div>
    <div class="site-title">
      <h1>GLIMMER OF LAUREL</h1>
      <p>Thoroughbred Racing Partnerships</p>
    </div>
  </header>

  <nav class="main-nav">
    <a href="#" class="home">HOME</a>
    <a href="#" class="about">ABOUT US</a>
    <a href="#" class="ownership">OWNERSHIP</a>
    <a href="#" class="roster">STABLE ROSTER</a>
    <a href="#" class="news">NEWS</a>
    <a href="#" class="contact">CONTACT US</a>
    <div class="nav-social">
      <span class="join">Join with us :</span>
      <span class="social-dot"></span>
      <span class="social-dot"></span>
      <span class="social-dot"></span>
      <span class="social-dot">
        <svg width="14" height="10" viewBox="0 0 14 10"><rect x="0.5" y="0.5" width="13" height="9" fill="none" stroke="#fff"/><path d="M0.5 0.5 L7 5.5 L13.5 0.5" fill="none" stroke="#fff"/></svg>
      </span>
    </div>
  </nav>

  <section class="hero">
    <div class="hero-photo" role="img" aria-label="Photo of a chestnut thoroughbred racehorse at full gallop with a jockey in red silks, a pack of racing horses faded in the background"></div>
    <h2 class="hero-title">EXPERIENCE THE THRILL OF OWNING A RACEHORSE</h2>
    <span class="slider-prev">
      <svg width="12" height="18" viewBox="0 0 12 18"><path d="M10 2 L3 9 L10 16" fill="none" stroke="#8aa3bd" stroke-width="2"/></svg>
    </span>
    <aside class="news-box">
      <h2>LATEST NEWS</h2>
      <div class="news-item">
        <svg width="12" height="12" viewBox="0 0 12 12"><path d="M1 2 L5 6 L1 10" fill="none" stroke="#999"/><line x1="10" y1="0" x2="10" y2="12" stroke="#ccc"/></svg>
        <div><a href="#">Curabitur eu ipsum pretium, gravida tortor eget.</a><time>October 22, 2013</time></div>
      </div>
      <div class="news-item">
        <svg width="12" height="12" viewBox="0 0 12 12"><path d="M1 2 L5 6 L1 10" fill="none" stroke="#999"/><line x1="10" y1="0" x2="10" y2="12" stroke="#ccc"/></svg>
        <div><a href="#">Curabitur eu ipsum pretium, gravida tortor eget.</a><time>October 22, 2013</time></div>
      </div>
      <div class="news-item">
        <svg width="12" height="12" viewBox="0 0 12 12"><path d="M1 2 L5 6 L1 10" fill="none" stroke="#999"/><line x1="10" y1="0" x2="10" y2="12" stroke="#ccc"/></svg>
        <div><a href="#">Curabitur eu ipsum pretium, gravida tortor eget.</a><time>October 22, 2013</time></div>
      </div>
    </aside>
  </section>

  <section class="welcome">
    <h2>WELCOME TO GOL PARTNERS</h2>
    <p>Nulla urna ligula, consequat quis consectetur ut, posuere et urna. Curabitur pellentesque vestibulum est quis posuere. Vestibulum vulputate ipsum eu dui commodo lacinia. Lorem ipsum dolor sit amet, consectetur adipiscing elit. Etiam posuere mauris eu nisi dignissim lacinia. Nunc vel orci ullamcorper turpis blandit gravida. Fusce congue rutrum mauris gravida tincidunt. Fusce quis nisi dictum, fringilla quam et, consectetur est. Ut quis odio eu justo aliquet volutpat. Donec aliquet vitae mi at elementum. Nam dapibus vehicula dolor, a iaculis nisl sodales et. Aliquam vitae blandit elit, quis ullamcorper nisl.</p>
  </section>

  <div class="video">
    <div class="video-still" role="img" aria-label="Video still of partners presenting a framed award"></div>
    <svg class="video-play" width="66" height="66" viewBox="0 0 66 66"><circle cx="33" cy="33" r="29" fill="none" stroke="#fff" stroke-width="5"/><path d="M25 19 L47 33 L25 47 Z" fill="#fff"/></svg>
  </div>

  <footer class="site-footer">
    <nav class="footer-nav">
      <a href="#">Home</a><a href="#">About Us</a><a href="#">Ownership</a><a href="#">Stable Roster</a><a href="#">News</a><a href="#">Contact us</a>
    </nav>
    <p class="copyright">Copyright &copy; GOL Partners. &nbsp; All rights reserved.</p>
    <div class="footer-social">
      <span class="social-dot"></span>
      <span class="social-dot"></span>
      <span class="social-dot"></span>
      <span class="social-dot">
        <svg width="14" height="10" viewBox="0 0 14 10"><rect x="0.5" y="0.5" width="13" height="9" fill="none" stroke="#1e1e1e"/><path d="M0.5 0.5 L7 5.5 L13.5 0.5" fill="none" stroke="#1e1e1e"/></svg>
      </span>
    </div>
  </footer>
</body>
</html>
```